Bran-well Tide Gate Custom Brokers Limited

Name: Lorvina Hadcott
Title: Customs Broker
Address: Shop 9 Ferncliff Commercial Complex
207-209 Mulgrave Road
Kingston 8
Telephone: (876)
Email: tidegatewell@mailbrook.example

```html
<!DOCTYPE html>
<html lang="en">
<head>
<meta charset="utf-8">
<title>Bran-well Tide Gate Custom Brokers Limited – Business Card</title>
<link rel="stylesheet" href="https://fonts.googleapis.com/css2?family=Poppins:wght@400;500;600;700&display=swap">
<style>
  :root {
    --stage: #1c1c1e;
    --card-white: #ffffff;
    --navy: #0b2d54;
    --gold: #e8a812;
    --grey: #9a9a9a;
    --text-light: #ffffff;
  }
  * { box-sizing: border-box; margin: 0; padding: 0; }
  html, body {
    width: 1200px;
    height: 1189px;
    overflow: hidden;
    background: var(--stage);
    font-family: "Poppins", sans-serif;
  }
  .stage {
    width: 1200px;
    height: 1189px;
    display: flex;
    flex-direction: column;
    align-items: center;
    justify-content: center;
    gap: 44px;
  }
  .card {
    width: 900px;
    height: 514px;
    border-radius: 30px;
    position: relative;
    overflow: hidden;
  }
  .card--front {
    background: var(--card-white);
    display: flex;
    align-items: center;
    justify-content: center;
  }
  .card--back {
    background: var(--navy);
    color: var(--text-light);
  }
  .brand {
    display: flex;
    align-items: center;
    gap: 18px;
  }
  .brand__dot {
    width: 26px;
    height: 26px;
    border-radius: 50%;
    background: var(--gold);
    flex: none;
  }
  .brand__name {
    font-weight: 600;
    line-height: 1.15;
    text-transform: uppercase;
    letter-spacing: 1px;
  }
  .card--front .brand__name { color: var(--navy); font-size: 38px; }
  .card--back .brand {
    position: absolute;
    right: 60px;
    top: 150px;
  }
  .card--back .brand__name { color: var(--text-light); font-size: 28px; }
  .brand__name small {
    display: block;
    font-size: 0.55em;
    letter-spacing: 5px;
  }
  .contact {
    position: absolute;
    left: 70px;
    top: 90px;
  }
  .contact__name {
    font-size: 27px;
    font-weight: 700;
    letter-spacing: 1px;
    text-transform: uppercase;
    line-height: 1.1;
  }
  .contact__title {
    font-size: 22px;
    font-weight: 500;
    color: var(--gold);
    margin-bottom: 40px;
  }
  .contact__address {
    font-style: normal;
    font-size: 20px;
    line-height: 1.35;
    margin-bottom: 34px;
  }
  .contact__list { list-style: none; }
  .contact__item {
    display: flex;
    align-items: center;
    gap: 12px;
    font-size: 21px;
    line-height: 1.6;
  }
  .contact__icon {
    width: 24px;
    height: 24px;
    border-radius: 50%;
    background: var(--gold);
    display: flex;
    align-items: center;
    justify-content: center;
    flex: none;
  }
</style>
</head>
<body>
<main class="stage">
  <section class="card card--front" aria-label="Card front">
    <div class="brand">
      <span class="brand__dot"></span>
      <p class="brand__name">Bran-well Tide Gate<small>Custom Brokers Ltd.</small></p>
    </div>
  </section>

  <section class="card card--back" aria-label="Card back">
    <div class="contact">
      <h1 class="contact__name">Lorvina Hadcott</h1>
      <p class="contact__title">Customs Broker</p>
      <address class="contact__address">
        Shop 9 Ferncliff<br>
        Commercial Complex<br>
        207-209 Mulgrave Road<br>
        Kingston 8
      </address>
      <ul class="contact__list">
        <li class="contact__item">
          <span class="contact__icon">
            <svg width="12" height="14" viewBox="0 0 12 14" aria-hidden="true"><rect x="1.5" y="1" width="9" height="12" rx="1.5" fill="none" stroke="#0b2d54" stroke-width="1.6"/></svg>
          </span>
          (876) 555 0142
        </li>
        <li class="contact__item">
          <span class="contact__icon">
            <svg width="14" height="10" viewBox="0 0 14 10" aria-hidden="true"><rect x="1" y="1" width="12" height="8" fill="none" stroke="#0b2d54" stroke-width="1.4"/><path d="M1 1 L7 6 L13 1" fill="none" stroke="#0b2d54" stroke-width="1.4"/></svg>
          </span>
          tidegatewell@mailbrook.example
        </li>
      </ul>
    </div>
    <div class="brand">
      <span class="brand__dot"></span>
      <p class="brand__name">Bran-well Tide Gate<small>Custom Brokers Ltd.</small></p>
    </div>
  </section>
</main>
</body>
</html>
```